Vesta PR Website

Vesta PR are a PR company with a requirement for a new website. In consultation with the client, we have defined a wireframe for a homepage to show content and functionality. A PDF of the wire frame is attached.
Current site http://www.vesta-pr.co.uk/
Updates
If you are using Stock Photography - please use iStock
Dear All
Unfortunately, my client didn't like any of the designs submitted.
I've uploaded 3 examples of the type of photography that will appear in the carousel as supplied by the client.
Target Market(s)
Business to Business/Professionals - high value clients
Number of Pages Required
1 page
Requirements
Must have
- Colour scheme is attached as a .ase file from Kuler and can be viewed on Kuler if you search for 'VESTA PR Palette'
Corporate Typeface is Futura Book - use of Cufon is OK
Current Logo to be reatainedCall 2 Action Buttons will be controlled via the CMS so a generic background may be useful for these.
Nice to have
- RSS feeds

```html
<!DOCTYPE html>
<html lang="en">
<head>
<meta charset="utf-8">
<title>Vesta PR – Home</title>
<link rel="stylesheet" href="https://fonts.googleapis.com/css2?family=Jost:wght@400;500&family=Noto+Sans:wght@400;700&display=swap">
<style>
:root{
  --teal:#5fb3aa;
  --teal-light:#a8dfd9;
  --teal-mid:#8fcfc7;
  --teal-deep:#4a9f96;
  --ink:#1c1c1c;
  --charcoal:#2b2b2b;
  --nav-top:#5a5a5a;
  --nav-bottom:#141414;
  --frame:#c9c9c9;
  --paper:#ffffff;
  --button-text:#c8f0ea;
  --photo-tone:#d9cbbd;
}
*{box-sizing:border-box;margin:0;padding:0}
html,body{width:1066px;height:1200px;overflow:hidden;background:var(--paper)}
body{font-family:"Noto Sans",Verdana,sans-serif;color:var(--ink)}
.page{position:relative;width:1000px;height:1126px;transform:scale(1.066);transform-origin:0 0}
.abs{position:absolute}
.futura{font-family:"Jost",sans-serif;font-weight:400}

/* header */
.site-header{left:0;top:0;width:1000px;height:111px;background:linear-gradient(#ffffff,#ececec);border-bottom:1px solid #d6d6d6}
.brand{left:28px;top:30px;display:flex;align-items:center;gap:14px}
.brand-name{font-family:"Jost",sans-serif;font-size:42px;letter-spacing:4px;color:var(--ink);line-height:1}
.brand-mark{width:22px;height:22px;background:var(--teal-light)}
.social{right:30px;top:28px;display:flex;gap:22px}
.social a{font-family:"Jost",sans-serif;font-size:19px;color:var(--teal-deep);text-decoration:none}
.call{right:30px;top:76px;font-size:25px;color:var(--ink)}

/* nav */
.main-nav{left:0;top:112px;width:1000px;height:44px;background:linear-gradient(var(--nav-top),var(--nav-bottom));display:flex;align-items:center;padding-left:35px}
.main-nav a{font-family:"Jost",sans-serif;font-size:17px;color:#fff;text-decoration:none;padding:0 10px}
.main-nav a:first-child{padding-left:0}
.main-nav .sep{width:1px;height:18px;background:#ddd;margin:0 10px}

/* content frame */
.frame{left:10px;top:150px;width:981px;height:778px;border-left:2px solid var(--frame);border-right:2px solid var(--frame)}

/* feature */
.feature{left:19px;top:148px;width:963px;height:223px;border-radius:6px;background:linear-gradient(#8fd3ca,#6fbcb3);padding:8px}
.feature-inner{width:100%;height:100%;border-radius:4px;background:linear-gradient(90deg,#6fbdb4,#8cd0c7 50%,#6fbdb4);position:relative}
.service-menu{left:8px;top:9px;width:284px}
.service-menu li{list-style:none;height:38px;line-height:38px;padding-left:17px;font-family:"Jost",sans-serif;font-size:23px;color:#123;background:linear-gradient(#a9e2db,#86cbc2);border-bottom:1px solid #6ab3aa}
.feature-title{left:356px;top:14px;font-size:22px;color:#1e2e2c;font-family:"Jost",sans-serif;font-weight:500}
.feature-copy{left:358px;top:48px;width:384px;font-size:12px;line-height:18px;color:#111}
.view-more{left:664px;top:192px;font-size:12px;font-weight:700;color:#111;text-decoration:underline}
.feature-photo{left:776px;top:9px;width:153px;height:192px;border:3px solid #fff;background:linear-gradient(#eef0f0,var(--photo-tone) 60%,#2a2a2a)}
.fade-band{left:19px;top:372px;width:963px;height:40px;background:linear-gradient(#d6efec,#ffffff)}

/* welcome */
.welcome-title{left:28px;top:396px;font-size:37px;color:var(--teal)}
.welcome-copy{left:29px;top:456px;width:605px;font-size:12.3px;line-height:14.6px}
.welcome-copy p{margin-bottom:14.6px}
.divider{left:648px;top:395px;height:453px;border-left:2px dotted #999}

/* cards */
.card{top:638px;width:277px;height:211px;border:1px solid #bcbcbc;border-radius:6px;background:linear-gradient(#ffffff,#dcdcdc);padding:14px 12px}
.card h2{font-size:23px;color:var(--ink);margin-bottom:14px;line-height:1.2}
.card p{font-size:12.3px;line-height:14.6px;margin-bottom:14.6px}
.client-news{left:32px}
.blog-entry{left:342px}
.blog-entry .narrow{width:140px}
.blog-photo{left:174px;top:32px;width:85px;height:88px;background:linear-gradient(#e3e6e8,#c9b6a2 55%,#4d5560)}

/* call to action */
.chevron{left:808px;width:24px;height:34px}
.c2a{left:703px;width:233px;height:68px;border-radius:4px;background:linear-gradient(#4a4a4a,#1c1c1c);padding:6px}
.c2a span{display:block;height:100%;background:linear-gradient(#444,#303030);border-radius:2px;font-family:"Jost",sans-serif;font-size:35px;color:var(--button-text);text-align:center;line-height:54px}

/* footer */
.site-footer{left:0;top:927px;width:1000px;height:156px;background:var(--teal-light)}
.footer-links{top:28px;list-style:none}
.footer-links li{font-size:12.5px;font-weight:700;line-height:24px}
.signup-title{left:614px;top:11px;font-size:35px;color:var(--ink)}
.email{left:615px;top:58px;width:289px;height:40px;border:1px solid #333;background:#fff;font-family:"Jost",sans-serif;font-size:22px;padding:4px 8px;line-height:30px}
.subscribe{left:613px;top:108px;width:147px;height:35px;border-radius:3px;background:linear-gradient(#555,#111);color:#fff;font-family:"Jost",sans-serif;font-size:22px;text-align:center;line-height:33px;border:1px solid #666}
.legal-bar{left:0;top:1082px;width:1000px;height:44px;background:linear-gradient(#4ea59b,#9ed8d1)}
.legal{right:20px;top:17px;font-size:12px;font-weight:700;color:#000}
</style>
</head>
<body>
<div class="page">

  <header class="site-header abs">
    <div class="brand abs"><span class="brand-name">Vesta PR</span><span class="brand-mark"></span></div>
    <nav class="social abs"><a href="#">Talkline</a><a href="#">Chirpnet</a><a href="#">Friendbook</a></nav>
    <div class="call abs futura">Call us now 0141 555 0198</div>
  </header>

  <nav class="main-nav abs">
    <a href="#">Home</a><span class="sep"></span>
    <a href="#">Vesta Services</a><span class="sep"></span>
    <a href="#">Press Office</a><span class="sep"></span>
    <a href="#">Vesta Case Studies</a><span class="sep"></span>
    <a href="#">Vesta People</a><span class="sep"></span>
    <a href="#">Blog</a><span class="sep"></span>
    <a href="#">Vesta News</a><span class="sep"></span>
    <a href="#">Contact Us</a>
  </nav>

  <div class="frame abs"></div>

  <section class="feature abs">
    <div class="feature-inner">
      <ul class="service-menu abs">
        <li>Online Public Relations</li>
        <li>Media Relations</li>
        <li>Consumer Campaigns</li>
        <li>Crisis Public Relations</li>
        <li>Internal Communications</li>
      </ul>
      <h1 class="feature-title abs">Online Public Relations</h1>
      <p class="feature-copy abs">Lorem Ipsum is simply dummy text of the printing and type-setting industry. Lorem Ipsum has been the industry's standard dummy text ever since the 1500s.<br>When an unknown printer took a galley of type and scrambled it to make a type specimen book. It has survived not only five centuries, but also the leap into electronic typesetting, remaining essentially unchanged.</p>
      <a class="view-more abs" href="#">View More</a>
      <div class="feature-photo abs" role="img" aria-label="Carousel photograph of a smiling businesswoman"></div>
    </div>
  </section>
  <div class="fade-band abs"></div>

  <h2 class="welcome-title abs futura">Welcome to Vesta PR</h2>
  <div class="welcome-copy abs">
    <p>Vesta Public Relations is one of Scotland’s leading independent agencies. Founded in 2000, we were determined to create a public relations service with a real difference – hence the name.</p>
    <p>Vesta Public Relation's trademark is a fresh, creative and hard working approach to public relations. It is an approach that secures real results for our clients.</p>
    <p>We are an agency with intelligence, integrity and imagination offering a comprehensive, results driven public relations service covering traditional and online public relations strategy and support.</p>
  </div>

  <article class="card client-news abs">
    <h2 class="futura">Client News</h2>
    <p>Phasellus sapien ipsum, interdum ut dapibus in, hendrerit nec nulla. Donec</p>
    <p>egestas scelerisque metus, nec placeratlectus ultrices ac. Nam sodales mollis euismod. Mauris ornare viverra dignissim.</p>
  </article>
  <article class="card blog-entry abs">
    <h2 class="futura">Blog Entry</h2>
    <p class="narrow">Phasellus sapien ipsum, interdum ut dapibus in, hendrerit nec nulla Donec.</p>
    <p>egestas scelerisque metus, nec placeratlectus ultrices ac. Nam sodales mollis euismod. Mauris ornare viverra dignissim.</p>
    <div class="blog-photo abs" role="img" aria-label="Portrait photograph of the blog author"></div>
  </article>

  <div class="divider abs"></div>

  <svg class="chevron abs" style="top:393px" viewBox="0 0 24 34"><path d="M2 2l10 9 10-9v8l-10 9-10-9z M2 14l10 9 10-9v8l-10 9-10-9z" fill="#777"/></svg>
  <a class="c2a abs" style="top:426px" href="#"><span>C2A Button</span></a>
  <svg class="chevron abs" style="top:505px" viewBox="0 0 24 34"><path d="M2 2l10 9 10-9v8l-10 9-10-9z M2 14l10 9 10-9v8l-10 9-10-9z" fill="#777"/></svg>
  <a class="c2a abs" style="top:539px" href="#"><span>C2A Button</span></a>
  <svg class="chevron abs" style="top:627px" viewBox="0 0 24 34"><path d="M2 2l10 9 10-9v8l-10 9-10-9z M2 14l10 9 10-9v8l-10 9-10-9z" fill="#777"/></svg>
  <a class="c2a abs" style="top:662px" href="#"><span>C2A Button</span></a>
  <svg class="chevron abs" style="top:745px" viewBox="0 0 24 34"><path d="M2 2l10 9 10-9v8l-10 9-10-9z M2 14l10 9 10-9v8l-10 9-10-9z" fill="#777"/></svg>
  <a class="c2a abs" style="top:779px" href="#"><span>C2A Button</span></a>

  <footer class="site-footer abs">
    <ul class="footer-links abs" style="left:35px">
      <li>Online Public Relations</li>
      <li>Media Relations</li>
      <li>Consumer Campaigns</li>
      <li>Crisis Public Relations</li>
      <li>Internal Communications</li>
    </ul>
    <ul class="footer-links abs" style="left:284px">
      <li>Subscribe to RSS Feed</li>
      <li>Our Friendbook page</li>
      <li>Link Three</li>
      <li>Link Four</li>
    </ul>
    <h2 class="signup-title abs futura">E-News Signup</h2>
    <div class="email abs">Email Address</div>
    <div class="subscribe abs">Subscribe</div>
  </footer>
  <div class="legal-bar abs">
    <div class="legal abs">© Copyright Notice | Site Credit | Legal</div>
  </div>

</div>
</body>
</html>
```